Upland Bird Hunting Preserve and Pointing Dog kennel

Need Price packages outlined for the bird hunting business. List the kennel and that we provide training and dogs for sale.
The preserve is "Tall Heron Provisions" the dog kennel is "Pine Hollow Setters"
1/2 Day Upland Field Hunts: 5 Pheasants $120
7 Chukar $125
Continental Hunt 12 Pheasants $325 includes meal, minimum 12 hunters
Guides available $100

Target Market(s)

upland bird hunters

Industry/Entity Type

hunting, outdoor

Colors
EE7325
F08F49
F5BC92
FAE3D3
FDF4ED

```html
<!DOCTYPE html>
<html lang="en">
<head>
<meta charset="utf-8">
<title>Tall Heron Provisions – Upland Bird Preserve</title>
<link href="https://fonts.googleapis.com/css2?family=Anton&family=Oswald:wght@400;500;600;700&display=swap" rel="stylesheet">
<style>
  :root {
    --mat: #9c9c9c;
    --paper: #e5ebd3;
    --sage: #c9d4ad;
    --olive: #4d5f27;
    --olive-mid: #6b7a3a;
    --footer: #5b6b2e;
    --gold: #c9a22b;
    --tick: #a8822a;
    --ink: #1c1c1c;
    --white: #ffffff;
  }
  * { box-sizing: border-box; margin: 0; padding: 0; }
  html, body { width: 981px; height: 1200px; overflow: hidden; }
  body { background: var(--mat); font-family: "Oswald", sans-serif; color: var(--ink); position: relative; }
  .poster { position: absolute; left: 89px; top: 88px; width: 802px; height: 1038px; background: var(--paper); overflow: hidden; }
  .abs { position: absolute; white-space: nowrap; }

  .photo-top { left: 0; top: 0; width: 802px; height: 340px;
    background: linear-gradient(180deg, #8f7a58 0%, #6d5a3e 55%, #3f3526 100%);
    clip-path: polygon(0 0, 100% 0, 100% 70%, 78% 76%, 55% 80%, 30% 88%, 0 97%); }
  .sage-wash { left: 0; top: 300px; width: 802px; height: 700px;
    background: radial-gradient(ellipse at 20% 30%, var(--sage) 0%, transparent 55%), radial-gradient(ellipse at 95% 60%, var(--sage) 0%, transparent 40%); opacity: .7; }

  .brand-title { left: 46px; top: 182px; font-family: "Anton", sans-serif; font-weight: 400; font-size: 63px; line-height: 67px;
    color: var(--gold); -webkit-text-stroke: 2px var(--white); paint-order: stroke fill; text-transform: uppercase; letter-spacing: -.5px; }
  .preserve-title { left: 46px; top: 393px; font-family: "Oswald", sans-serif; font-weight: 700; font-size: 44px; line-height: 51px;
    color: var(--olive); -webkit-text-stroke: 1.5px var(--white); paint-order: stroke fill; text-transform: uppercase; letter-spacing: -1px; }

  .continental-title { left: 46px; top: 513px; font-weight: 700; font-size: 28px; line-height: 36px; letter-spacing: -.4px; }
  .continental-title span { color: var(--olive-mid); }
  .feature-pill { top: 563px; height: 48px; border: 1.5px solid var(--olive-mid); border-radius: 12px;
    padding: 4px 0 0 21px; font-size: 16px; line-height: 19px; }
  .feature-pill .tick { position: absolute; left: -10px; top: 14px; width: 20px; height: 20px; }
  .feature-notes { left: 46px; top: 620px; font-size: 16px; display: flex; gap: 14px; }
  .feature-notes span { display: flex; align-items: center; gap: 5px; }

  .contact-bar { left: 40px; top: 664px; width: 402px; height: 52px; border-radius: 12px; overflow: hidden;
    background: linear-gradient(90deg, var(--olive) 0 47%, var(--ink) 47% 100%); display: flex; align-items: center;
    color: var(--white); font-weight: 600; font-size: 29px; line-height: 52px; letter-spacing: -.6px; }
  .contact-name { padding-left: 18px; width: 172px; flex: none; }
  .contact-icon { width: 36px; height: 36px; margin: 0 10px 0 0; flex: none; }
  .contact-phone { flex: none; }

  .packages-title { left: 487px; top: 292px; font-weight: 700; font-size: 37px; line-height: 44px; letter-spacing: -.5px; }
  .packages-sub { left: 487px; top: 336px; font-weight: 700; font-size: 37px; line-height: 44px; color: var(--olive-mid); letter-spacing: -.5px; }
  .price-box { width: 134px; height: 81px; border: 1.5px solid var(--olive-mid); border-radius: 12px; text-align: center; }
  .price-box .label { font-weight: 600; font-size: 19px; line-height: 22px; padding-top: 8px; }
  .price-box .amount { font-weight: 700; font-size: 38px; line-height: 44px; color: var(--gold); }
  .guide { left: 630px; top: 484px; }
  .guide .label { font-weight: 600; font-size: 20px; line-height: 28px; }
  .guide .amount { display: flex; align-items: center; gap: 6px; color: var(--olive); font-weight: 700; }
  .guide .amount b { font-size: 44px; line-height: 46px; }
  .guide .amount small { font-size: 16px; line-height: 17px; font-weight: 600; }

  .kennel-name { left: 487px; top: 612px; width: 274px; text-align: center; font-weight: 500; font-size: 21px; line-height: 30px; letter-spacing: 2px; }
  .kennel-rule { left: 528px; top: 680px; width: 193px; height: 3px; background: var(--ink); }
  .kennel-town { left: 487px; top: 686px; width: 274px; text-align: center; font-size: 19px; line-height: 26px; letter-spacing: 1px; }
  .kennel-pitch { left: 487px; top: 722px; width: 274px; text-align: center; font-weight: 700; font-size: 27px; line-height: 31px; letter-spacing: -.4px; }
  .kennel-pitch span { color: var(--olive-mid); }

  .photo-hunters { left: 0; top: 732px; width: 480px; height: 260px;
    background: linear-gradient(180deg, #8b7558 0%, #6a563e 60%, #4f4232 100%);
    clip-path: polygon(0 14%, 40% 6%, 60% 0, 100% 14%, 96% 60%, 100% 100%, 0 100%); }
  .photo-dog { left: 527px; top: 800px; width: 275px; height: 192px;
    background: linear-gradient(180deg, #b8a47a 0%, #c9a65a 55%, #8f7540 100%);
    clip-path: polygon(8% 6%, 100% 0, 100% 100%, 0 100%, 3% 40%); }
  .grass { left: 0; top: 968px; width: 802px; height: 22px; }
  .footer { left: 0; top: 987px; width: 802px; height: 51px; background: var(--footer); color: var(--white);
    display: flex; align-items: center; justify-content: center; gap: 8px; font-weight: 600; font-size: 22px; letter-spacing: -.2px; }
</style>
</head>
<body>
<main class="poster">
  <div class="abs sage-wash"></div>
  <div class="abs photo-top" role="img" aria-label="Photo of a group of hunters standing behind a log lined with harvested pheasants in a winter woodland"></div>

  <h1 class="abs brand-title">Tall Heron<br>Provisions, LLC<br>Millbrook, MO</h1>
  <h2 class="abs preserve-title">Licensed Upland<br>Bird Preserve</h2>

  <h3 class="abs continental-title">Continental <span>Pheasant Hunt</span></h3>
  <div class="abs feature-pill" style="left:49px;width:103px;">
    <svg class="tick" viewBox="0 0 20 20"><circle cx="10" cy="10" r="10" fill="#a8822a"/><path d="M5.5 10.3l3 3 6-6" fill="none" stroke="#fff" stroke-width="2"/></svg>
    12 hunter<br>minimum</div>
  <div class="abs feature-pill" style="left:165px;width:102px;">
    <svg class="tick" viewBox="0 0 20 20"><circle cx="10" cy="10" r="10" fill="#a8822a"/><path d="M5.5 10.3l3 3 6-6" fill="none" stroke="#fff" stroke-width="2"/></svg>
    $325<br>per hunter</div>
  <div class="abs feature-pill" style="left:281px;width:151px;">
    <svg class="tick" viewBox="0 0 20 20"><circle cx="10" cy="10" r="10" fill="#a8822a"/><path d="M5.5 10.3l3 3 6-6" fill="none" stroke="#fff" stroke-width="2"/></svg>
    Includes 12<br>pheasants and meal</div>
  <div class="abs feature-notes">
    <span><svg width="16" height="16" viewBox="0 0 16 16"><path d="M8 1l7 7-7 7-7-7z" fill="none" stroke="#4d5f27" stroke-width="1.4"/><path d="M5 8l2 2 4-4" fill="none" stroke="#4d5f27" stroke-width="1.4"/></svg>All hunts include bird Cleaning</span>
    <span><svg width="16" height="16" viewBox="0 0 16 16"><path d="M8 1l7 7-7 7-7-7z" fill="none" stroke="#4d5f27" stroke-width="1.4"/><path d="M5 8l2 2 4-4" fill="none" stroke="#4d5f27" stroke-width="1.4"/></svg>Lodging available</span>
  </div>

  <div class="abs contact-bar">
    <span class="contact-name">Dale Morgan</span>
    <svg class="contact-icon" viewBox="0 0 38 38"><circle cx="19" cy="19" r="18" fill="#c9a22b"/><circle cx="19" cy="19" r="13" fill="none" stroke="#fff" stroke-width="2"/><path d="M14 12c1-1 2-1 2.6 0l1.6 2.6c.4.7.2 1.4-.4 1.9l-1 .8c.8 2 2.2 3.4 4 4.2l.9-1c.5-.6 1.2-.7 1.9-.3l2.5 1.6c.9.6 1 1.6 0 2.6-1.6 1.6-3.6 1.8-6.3.3-3.3-1.8-5.9-5-6.8-8.3-.4-1.6 0-2.9 1-3.9z" fill="#fff"/></svg>
    <span class="contact-phone">660-555-0148</span>
  </div>

  <h2 class="abs packages-title">Hunting Packages</h2>
  <p class="abs packages-sub">1/2-day field hunts</p>
  <div class="abs price-box" style="left:485px;top:392px;"><div class="label">5 Pheasants</div><div class="amount">$120</div></div>
  <div class="abs price-box" style="left:626px;top:392px;"><div class="label">7 Chukar</div><div class="amount">$125</div></div>
  <div class="abs price-box" style="left:485px;top:480px;"><div class="label">10 Quail</div><div class="amount">$125</div></div>
  <div class="abs guide">
    <div class="label">Guide Available</div>
    <div class="amount"><b>$100</b><small>per<br>half day</small></div>
  </div>

  <div class="abs kennel-name">PINE HOLLOW SETTERS</div>
  <div class="abs kennel-rule"></div>
  <div class="abs kennel-town">FERNHILL, MO</div>
  <p class="abs kennel-pitch">Training, puppies and<br>started dogs <span>available</span></p>

  <div class="abs photo-hunters" role="img" aria-label="Photo of two hunters and a pointing dog behind a log lined with harvested quail in the woods"></div>
  <div class="abs photo-dog" role="img" aria-label="Photo of a ticked shorthaired pointer wearing an orange collar in tall golden grass"></div>
  <svg class="abs grass" viewBox="0 0 802 22" preserveAspectRatio="none"><path d="M0 22V14l10-8 6 9 9-12 7 11 10-9 6 10 11-13 6 12 9-8 8 9 10-11 7 12 9-9 8 8 11-12 6 13 10-10 7 9 9-12 8 11 10-9 7 10 9-13 8 12 10-8 6 9 11-11 7 11 9-10 8 10 10-12 6 12 10-9 8 9 9-11 7 12 11-10 6 9 10-12 8 11 9-9 7 10 10-13 8 12 9-8 7 9 10-11 8 11 9-10 7 10 11-12 6 12 10-9 7 9 9-11 8 12 10-10 7 9 9-12 8 11 10-9 6 10 10-13 8 12 9-8 8 9 10-11 7 11 9-10 8 10 10-12 7 12 9-9 8 9 10-11 6 12 11-10 7 9 9-12 8 11 10-9 7 10 9-13 8 12 10-8 6 9 11-11 7 11 9-10 8 10 10-12 7 12 9-9 8 10V22z" fill="#5b6b2e"/></svg>

  <footer class="abs footer">
    <svg width="20" height="24" viewBox="0 0 20 24"><path d="M10 0C4.5 0 1 4 1 8.6 1 14.6 10 24 10 24s9-9.4 9-15.4C19 4 15.5 0 10 0z" fill="#c9a22b"/><circle cx="10" cy="8.6" r="3.6" fill="#5b6b2e"/></svg>
    <span>1450 Cedar Bend Road, Millbrook, MO &nbsp;|&nbsp; zip code-65099</span>
  </footer>
</main>
</body>
</html>
```